I need an Office Furniture selling website

My office furniture store is driven by creativity and innovation. With this i am searching for an industry standard website for my office furniture and items selling website. I sell a wide range of office furniture items such as chairs, tables, burglary, cotton, wardrobe, etc. There will be a category for each of the items i sell. My business is based in the United States and services only US based residents. I don't accept online payments and customers are to pay on delivery of items. The website is to have images of the items i sell. I would like brown, black and golden colors because those are the colors furniture mostly make use of. Designs submitted should be unique.

Industry/Entity Type

Furniture Store

Coding

Coded - Design and coding required

```html
<!DOCTYPE html>
<html lang="en">
<head>
<meta charset="utf-8">
<title>Office Furniture</title>
<link href="https://fonts.googleapis.com/css2?family=Oswald:wght@300&family=Roboto:wght@400;500&display=swap" rel="stylesheet">
<style>
:root{
  --maroon:#6b1414;
  --gold:#b79a3c;
  --gold-soft:#3a321a;
  --ink:#111111;
  --grey-bg:#efefef;
  --text:#666666;
  --line:#d9d9d9;
  --footer:#121212;
  --footer-text:#bdbdbd;
}
*{margin:0;padding:0;box-sizing:border-box}
html,body{width:677px;height:1200px;overflow:hidden}
body{font-family:"Roboto",Arial,sans-serif;background:#fff;color:var(--text);position:relative}
.wrap{width:590px;margin:0 auto;position:relative}

.site-header{height:70px}
.logo{position:absolute;left:0;top:21px;font-family:"Oswald",sans-serif;font-weight:300;font-size:28px;color:var(--gold);letter-spacing:.2px;line-height:1}
.call{position:absolute;right:3px;top:12px;font-size:13px;color:var(--maroon);font-weight:500}
.call span{color:var(--gold);font-weight:400}
.search{position:absolute;right:0;top:35px;width:156px;height:27px;border:1px solid #cfcfcf;background:#f3f3f3;font-size:9px;color:#999;padding:8px 9px}
.search svg{position:absolute;right:6px;top:6px}

.main-nav{background:var(--maroon);height:35px}
.main-nav ul{list-style:none;display:flex;height:35px}
.main-nav li{color:#fff;font-size:10px;padding:0 16px 0 20px;line-height:35px;font-weight:500;position:relative}
.main-nav li+li::before{content:"";position:absolute;left:0;top:8px;height:19px;width:1px;background:rgba(255,255,255,.2)}
.main-nav li.active{background:var(--gold);padding:0 19px}

.hero{height:282px;position:relative;background:
  radial-gradient(ellipse 150px 75px at 150px 200px,rgba(20,20,20,.85) 0%,rgba(20,20,20,.6) 55%,rgba(20,20,20,0) 100%),
  radial-gradient(ellipse 130px 45px at 380px 120px,rgba(190,190,190,.9) 0%,rgba(190,190,190,0) 100%),
  radial-gradient(ellipse 70px 50px at 610px 95px,rgba(70,110,40,.55) 0%,rgba(70,110,40,0) 100%),
  linear-gradient(180deg,#ece6d2 0%,#d8cfa8 14%,#b9ab6a 32%,#c9bf98 48%,#ddd6c7 62%,#ece7de 100%)}
.hero-arrow{position:absolute;top:137px;width:26px;height:26px;border:1.5px solid #fff;border-radius:50%}
.hero-arrow svg{position:absolute;left:7px;top:7px}
.hero-arrow.prev{left:9px}.hero-arrow.next{right:9px}

.welcome{background:var(--grey-bg);height:185px;text-align:center;padding-top:34px}
.welcome h1,.section-title{font-weight:400;font-size:23px;color:var(--maroon);letter-spacing:.2px}
.welcome h1 span,.section-title span{color:var(--gold)}
.welcome p{width:510px;margin:9px auto 0;font-size:8.4px;line-height:15.2px;color:#777}
.btn{display:inline-block;background:var(--gold);color:#fff;font-size:11px;font-weight:500}
.welcome .btn{margin-top:6px;width:101px;height:32px;line-height:32px;font-size:11.5px;font-weight:400}

.products{padding-top:23px;text-align:center}
.grid{display:grid;grid-template-columns:repeat(4,141px);gap:10px 9px;margin-top:14px;text-align:left}
.card{height:176px;border:1px solid var(--line);position:relative}
.card .photo{position:absolute;left:15px;top:8px;width:110px;height:112px}
.card .name{position:absolute;left:1px;top:136px;font-size:14px;color:var(--maroon)}
.card .price{position:absolute;left:2px;top:155px;font-size:10.5px;color:var(--gold)}
.card .btn{position:absolute;right:-1px;top:135px;width:68px;height:32px;line-height:32px;text-align:center;font-size:11.5px;font-weight:400}

.site-footer{position:absolute;left:0;top:1032px;width:677px;height:168px;background:var(--footer)}
.cols{display:grid;grid-template-columns:150px 150px 150px 140px;padding-top:19px}
.cols h4{color:var(--gold);font-size:9.5px;font-weight:500;margin-bottom:10px}
.links{list-style:none;font-size:8px;color:#ddd;line-height:12.9px}
.links li::before{content:"»";color:var(--gold);margin-right:5px}
.contact div{position:relative;padding-left:19px;font-size:8px;color:var(--footer-text);line-height:12px;margin-bottom:6px}
.contact svg{position:absolute;left:0;top:1px}
.contact .org{color:#ddd;font-size:8.5px;letter-spacing:.3px}
.newsletter p{font-size:8.3px;line-height:14px;color:var(--footer-text)}
.subscribe{margin-top:8px;width:140px;height:32px;border:1px solid #ccc;display:flex;background:#111}
.subscribe span{flex:1;font-size:8px;color:#ddd;line-height:30px;padding-left:7px}
.subscribe i{width:32px;background:var(--gold);position:relative}
.subscribe svg{position:absolute;left:8px;top:7px}
.social div{display:flex;align-items:center;font-size:8.5px;color:#ddd;margin-bottom:5px}
.social b{width:23px;height:23px;border-radius:50%;border:1.5px solid var(--gold);background:var(--gold-soft);margin-right:9px}
.social div:first-of-type b{background:var(--gold)}
.copy{position:absolute;left:43px;top:133px;width:590px;border-top:1px solid #333;text-align:center;font-size:8px;color:#ccc;padding-top:12px}
.copy span{color:var(--gold)}
</style>
</head>
<body>
<header class="site-header">
  <div class="wrap">
    <div class="logo">OFFICE FURNITURE</div>
    <div class="call">Call us: <span>123 456 789</span></div>
    <div class="search">Search
      <svg width="13" height="13" viewBox="0 0 13 13"><circle cx="5.5" cy="5.5" r="4" fill="none" stroke="#6b1414" stroke-width="1.8"/><line x1="8.5" y1="8.5" x2="12" y2="12" stroke="#6b1414" stroke-width="2"/></svg>
    </div>
  </div>
</header>

<nav class="main-nav">
  <div class="wrap">
    <ul>
      <li class="active">HOME</li><li>ABOUT US</li><li>PRODUCT</li><li>FREE ESTIMATE</li><li>NEWS</li><li>CONTACT US</li>
    </ul>
  </div>
</nav>

<section class="hero" role="img" aria-label="Bright office lobby with black leather armchairs and a reception desk">
  <div class="hero-arrow prev"><svg width="10" height="10" viewBox="0 0 10 10"><polyline points="6.5,1 2.5,5 6.5,9" fill="none" stroke="#fff" stroke-width="1.4"/></svg></div>
  <div class="hero-arrow next"><svg width="10" height="10" viewBox="0 0 10 10"><polyline points="3.5,1 7.5,5 3.5,9" fill="none" stroke="#fff" stroke-width="1.4"/></svg></div>
</section>

<section class="welcome">
  <h1>WELCOME TO <span>OFFICE FURNITURE</span></h1>
  <p>Lorem Ipsum is simply dummy text of the printing and typesetting industry. Lorem Ipsum has been the industry's standard dummy text ever since the 1500s, when an unknown printer took a galley of type and scrambled it to make a type specimen book. It has survived not only five centuries, but also the leap into electronic.</p>
  <span class="btn">KNOW MORE</span>
</section>

<section class="products">
  <div class="wrap">
    <h2 class="section-title">OUR <span>PRODUCT</span></h2>
    <div class="grid">
      <div class="card"><div class="photo" role="img" aria-label="Black curved cantilever chair" style="background:radial-gradient(ellipse 30% 45% at 50% 50%,#1e1e1e 0%,#2a2a2a 60%,rgba(255,255,255,0) 100%)"></div><div class="name">Chairs</div><div class="price">$25.89</div><span class="btn">DETAIL</span></div>
      <div class="card"><div class="photo" role="img" aria-label="Stack of striped cotton throws" style="background:radial-gradient(ellipse 42% 38% at 50% 50%,#b3372c 0%,#2a4d8f 45%,#1c3a2e 70%,rgba(255,255,255,0) 100%)"></div><div class="name">Cotton</div><div class="price">$25.89</div><span class="btn">DETAIL</span></div>
      <div class="card"><div class="photo" role="img" aria-label="Black steel safe with open door" style="background:radial-gradient(ellipse 42% 40% at 50% 50%,#151515 0%,#222 65%,rgba(255,255,255,0) 100%)"></div><div class="name">Burglary</div><div class="price">$25.89</div><span class="btn">DETAIL</span></div>
      <div class="card"><div class="photo" role="img" aria-label="Dark wooden side table with curved legs" style="background:radial-gradient(ellipse 42% 40% at 50% 45%,#1a1412 0%,#2e241f 65%,rgba(255,255,255,0) 100%)"></div><div class="name">Table</div><div class="price">$25.89</div><span class="btn">DETAIL</span></div>
      <div class="card"><div class="photo" role="img" aria-label="Black chair with carved openwork back" style="background:radial-gradient(ellipse 32% 46% at 50% 50%,#0c0c0c 0%,#222 60%,rgba(255,255,255,0) 100%)"></div><div class="name">Chairs</div><div class="price">$25.89</div><span class="btn">DETAIL</span></div>
      <div class="card"><div class="photo" role="img" aria-label="Folded grey cotton blanket with fringe" style="background:radial-gradient(ellipse 42% 38% at 50% 50%,#bdbdbd 0%,#d4d4d4 60%,rgba(255,255,255,0) 100%)"></div><div class="name">Cotton</div><div class="price">$25.89</div><span class="btn">DETAIL</span></div>
      <div class="card"><div class="photo" role="img" aria-label="Tall dark wood wardrobe" style="background:radial-gradient(ellipse 30% 50% at 50% 50%,#3c2a20 0%,#4a3226 65%,rgba(255,255,255,0) 100%)"></div><div class="name">Wardrobe</div><div class="price">$25.89</div><span class="btn">DETAIL</span></div>
      <div class="card"><div class="photo" role="img" aria-label="Round black pedestal table" style="background:radial-gradient(ellipse 46% 40% at 50% 45%,#0f0f0f 0%,#2a2a2a 60%,rgba(255,255,255,0) 100%)"></div><div class="name">Table</div><div class="price">$25.89</div><span class="btn">DETAIL</span></div>
    </div>
  </div>
</section>

<footer class="site-footer">
  <div class="wrap cols">
    <div>
      <h4>USEFULL LINKS</h4>
      <ul class="links"><li>Homel</li><li>About Us</li><li>Product</li><li>Free Estimate</li><li>News</li><li>Contact Us</li></ul>
    </div>
    <div class="contact">
      <h4>GET IN TOUCH</h4>
      <div><svg width="9" height="11" viewBox="0 0 9 11"><path d="M4.5 10.5C2 7 1 5.5 1 4a3.5 3.5 0 0 1 7 0c0 1.5-1 3-3.5 6.5z" fill="none" stroke="#b79a3c"/><circle cx="4.5" cy="4" r="1.2" fill="#b79a3c"/></svg><span class="org">OFFICE FURNITURE</span><br>Lorem ipsum dolor amet simple.</div>
      <div><svg width="10" height="10" viewBox="0 0 10 10"><path d="M2 1l2 2-1 1.5c.8 1.5 1.5 2.2 3 3L7.5 6l2 2-1.5 1.5C4.5 9 1 5.5.5 2z" fill="none" stroke="#b79a3c" stroke-width=".9"/></svg>+(91) 123 456 7890</div>
      <div><svg width="10" height="10" viewBox="0 0 10 10"><rect x="1" y="3.5" width="8" height="4" fill="none" stroke="#b79a3c" stroke-width=".9"/><rect x="2.5" y="1" width="5" height="2.5" fill="none" stroke="#b79a3c" stroke-width=".9"/><rect x="2.5" y="6" width="5" height="3" fill="none" stroke="#b79a3c" stroke-width=".9"/></svg>+(91) 123 456 7890</div>
      <div><svg width="10" height="9" viewBox="0 0 10 9"><rect x=".5" y="1" width="9" height="7" fill="none" stroke="#b79a3c" stroke-width=".9"/><polyline points=".5,1 5,5 9.5,1" fill="none" stroke="#b79a3c" stroke-width=".9"/></svg>info@officefurniturestore.test</div>
    </div>
    <div class="newsletter">
      <h4>NEWSLETTER</h4>
      <p>Subscribe to stay on Harbor &amp; Pine Home Services, LLC</p>
      <div class="subscribe"><span>Enter your Email</span><i><svg width="17" height="17" viewBox="0 0 17 17"><polygon points="1,8 16,1 11,16 8,10" fill="none" stroke="#fff" stroke-width="1.3" stroke-linejoin="round"/><line x1="8" y1="10" x2="16" y2="1" stroke="#fff" stroke-width="1.3"/></svg></i></div>
    </div>
    <div class="social">
      <h4>FOLLOW US</h4>
      <div><b></b>Facepage</div>
      <div><b></b>Chirper</div>
      <div><b></b>Linkfolio</div>
    </div>
  </div>
  <div class="copy">© 2016 <span>Office Furniture</span> -  All rights reserved.</div>
</footer>
</body>
</html>
```